Transform Your Giving

I need a tri-fold brochure that will fit in a standard number 10 business envelope. Meadowlark and Allied Services is a charitable nonprofit. The goal of this brochure is to stimulate people into thinking about other ways to make a donation. The design should communicate the essential information on donation options, create a sense of professional integrity, be graphically sharp, easy to read and laid out in a way that doesn't make the material appear crowded.

```html
<!DOCTYPE html>
<html lang="en">
<head>
<meta charset="utf-8">
<title>Transform Your Giving – Tri-fold Brochure</title>
<link rel="stylesheet" href="https://fonts.googleapis.com/css2?family=Poppins:ital,wght@0,400;0,500;0,600;0,700;0,800;1,400&family=Montserrat:wght@800;900&display=swap">
<style>
:root{
  --navy:#2b2170;
  --navy-deep:#221a5e;
  --ink:#27206a;
  --green:#3cc13b;
  --green-dark:#2ea82e;
  --paper:#ffffff;
  --mist:#f2f2f4;
  --stage:#ececee;
  --text:#222;
}
*{box-sizing:border-box;margin:0;padding:0}
html,body{width:694px;height:1200px;overflow:hidden}
body{background:var(--stage);font-family:"Poppins",sans-serif;color:var(--text);position:relative}
.spread{position:absolute;left:17px;width:660px;height:287px;display:flex;box-shadow:0 2px 6px rgba(0,0,0,.18)}
.spread--outside{top:293px}
.spread--inside{top:620px}
.panel{position:relative;width:220px;height:100%;overflow:hidden}
.panel--navy{background:var(--navy);color:#fff}
.panel--light{background:var(--mist)}
.panel--white{background:var(--paper)}

/* Impact panel */
.impact-title{position:absolute;left:17px;top:16px;font-weight:700;font-size:11.3px;letter-spacing:-.2px;color:var(--green)}
.impact-title span{color:#fff}
.impact-copy{position:absolute;left:19px;top:35px;width:190px;font-size:7px;line-height:1.18}
.photo{position:absolute}
.photo--carers{left:0;top:106px;width:128px;height:181px;background:linear-gradient(160deg,#3a4fa0 0%,#5876b8 45%,#2d3f8a 100%)}
.accent-triangle{position:absolute;left:0;top:106px}
.options{position:absolute;left:137px;top:82px;width:66px;height:215px;border:1px solid var(--green);border-bottom:none;border-radius:6px 6px 0 0;display:flex;flex-direction:column;align-items:center;padding-top:8px;gap:5px}
.option{display:flex;flex-direction:column;align-items:center;font-size:6.4px;line-height:1.15;text-align:center;color:#e8e8f4}
.option svg{width:16px;height:16px;margin-bottom:2px}

/* Contact panel */
.invite{position:absolute;left:10px;top:17px;width:200px;text-align:center;font-size:7.3px;line-height:1.2;font-weight:600}
.invite .hl{color:var(--green)}
.quote{position:absolute;left:25px;top:80px;width:158px;height:34px;border:1px solid var(--green);border-radius:4px;text-align:center;font-style:italic;font-size:7.5px;line-height:1.2;padding-top:4px}
.quote-mark{position:absolute;font-size:13px;font-weight:700;color:var(--green);font-style:normal;line-height:1}
.quote-mark--open{left:-4px;top:-9px}
.quote-mark--close{right:-4px;bottom:-14px}
.quote-author{position:absolute;left:0;top:114px;width:220px;text-align:center;font-size:7.8px;font-weight:600;color:var(--green)}
.quote-author::before,.quote-author::after{content:"";display:inline-block;width:18px;height:1px;background:var(--green);vertical-align:middle;margin:0 4px}
.will{position:absolute;left:0;top:128px;width:220px;text-align:center;font-size:6.4px;font-weight:500;line-height:1.25}
.will-url{display:block;font-size:10px;font-weight:700;color:var(--green);letter-spacing:.6px;line-height:1.2}
.contact-box{position:absolute;left:12px;top:166px;width:193px;height:130px;border:1px solid var(--green);border-bottom:none;border-radius:10px 10px 0 0}
.contact-tab{position:absolute;left:56px;top:-7px;width:80px;height:13px;background:var(--green);border-radius:0 0 7px 7px;font-size:6.6px;font-weight:700;text-align:center;letter-spacing:.8px;line-height:13px}
.contact-head{position:absolute;top:16px;width:100%;text-align:center;font-size:6.6px;font-weight:600;line-height:1.1}
.contact-head small{display:block;font-size:5.1px;font-weight:400;color:#ddd}
.contact-list{position:absolute;left:16px;top:43px;list-style:none;font-size:5.6px;line-height:1.2}
.contact-list li{display:flex;gap:4px;margin-bottom:3px}
.contact-list svg{width:6px;height:6px;flex:none;margin-top:1px}
.follow{position:absolute;right:12px;top:83px;font-size:5.8px;text-align:center}
.social{display:flex;gap:3px;justify-content:center;margin-top:3px}
.social span{width:11px;height:11px;border-radius:50%;background:var(--green)}
.disclaimer{position:absolute;left:16px;top:110px;width:160px;font-size:2.6px;line-height:1.25;color:#cfcde4}

/* Cover panel */
.org-name{position:absolute;left:0;top:18px;width:220px;text-align:center;font-size:8.6px;font-weight:700;color:var(--ink);line-height:1.15}
.org-name .dot{display:inline-block;width:7px;height:7px;border-radius:50%;background:var(--green);margin-right:4px;vertical-align:0}
.cover-title{position:absolute;left:0;top:60px;width:220px;text-align:center;font-family:"Montserrat",sans-serif;font-weight:900;line-height:.95}
.cover-title .l1{display:block;color:var(--green);font-size:19px}
.cover-title .l2{display:block;color:var(--ink);font-size:22.5px;letter-spacing:-.3px}
.tagline{position:absolute;left:0;top:107px;width:220px;text-align:center;font-size:8px;letter-spacing:1.5px;color:var(--ink);font-weight:500}
.tagline i{color:var(--green);font-style:normal;margin:0 4px}
.discover{position:absolute;left:20px;top:126px;width:180px;text-align:center;font-size:6.9px;line-height:1.15;color:#222}
.photo--couple{left:20px;top:147px;width:190px;height:140px;background:linear-gradient(180deg,#e6e6ea 0%,#c9ccd8 50%,#9ea8c2 100%)}
.float-icon{position:absolute;width:19px;height:19px;border-radius:50%;background:#fff;border:1px solid #dfe8df;display:flex;align-items:center;justify-content:center}
.float-icon svg{width:12px;height:12px}
.url-pill{position:absolute;left:42px;top:260px;width:137px;height:14px;border-radius:7px;background:var(--green);color:#fff;text-align:center;font-size:8px;font-weight:700;letter-spacing:1px;line-height:14px}

/* Inside panels */
.intro{position:absolute;left:18px;top:17px;width:184px;font-size:6.8px;line-height:1.18}
.feature-kicker{color:var(--green);font-weight:700;line-height:1.1}
.feature-main{color:var(--ink);font-weight:800;line-height:1}
.stocks-head{position:absolute;left:19px;top:67px}
.stocks-head .feature-kicker{font-size:9.6px}
.stocks-head .feature-main{font-size:15.5px;margin-top:2px}
.chart{position:absolute;left:120px;top:70px;width:95px;height:75px}
.body-copy{font-size:6.7px;line-height:1.2}
.body-copy strong{font-weight:600;color:#111}
.body-copy h4{font-size:7.3px;font-weight:600;margin-top:4px;color:#111}
.stocks-copy{position:absolute;left:19px;top:147px;width:190px}

.daf-head{position:absolute;left:11px;top:14px}
.daf-head .feature-kicker{font-size:13.4px;line-height:1}
.daf-head .feature-main{font-size:12px;margin-top:3px;line-height:1.05}
.bank-art{position:absolute;left:125px;top:13px;width:58px;height:58px;background:linear-gradient(180deg,#5b8fd6,#d7e3f4);border-radius:4px}
.daf-copy{position:absolute;left:11px;top:76px;width:200px;font-size:5.9px;line-height:1.18}
.daf-copy strong{font-weight:600}
.daf-copy h4{font-size:5.9px;font-weight:600}
.qcd-art{position:absolute;left:11px;top:155px;width:32px;height:32px;background:linear-gradient(160deg,#f5c542,#e9874a);border-radius:4px}
.qcd-head{position:absolute;left:47px;top:155px;width:165px}
.qcd-head .feature-kicker{font-size:8.2px;line-height:1.1}
.qcd-head .feature-main{font-size:5.4px}
.qcd-head p{font-size:5.6px;line-height:1.15}
.qcd-copy{position:absolute;left:11px;top:197px;width:200px;font-size:4.6px;line-height:1.2}
.qcd-copy h4{font-size:4.6px;font-weight:600}

.gift-block{position:absolute;left:11px;width:200px}
.gift-block--crypto{top:15px}
.gift-block--annuity{top:158px}
.gift-head{display:flex;gap:5px;align-items:flex-start}
.gift-art{width:23px;height:23px;flex:none;border-radius:50%}
.gift-art--coin{background:radial-gradient(circle,#f8c93a,#e59c1c)}
.gift-art--box{border-radius:3px;background:linear-gradient(180deg,#f24f3a,#f8a23a)}
.gift-head .feature-kicker{font-size:8.4px}
.gift-head .feature-main{font-size:8.4px;color:#fff;font-weight:700}
.gift-head p{font-size:5.3px;line-height:1.15;color:#e8e8f4}
.gift-copy{font-size:4.7px;line-height:1.2;margin-top:3px;color:#eaeaf5}
.gift-copy h4{font-size:4.7px;font-weight:600;margin-top:3px}
.gift-copy p+p{margin-top:3px}
</style>
</head>
<body>

<!-- Outside spread -->
<section class="spread spread--outside">
  <article class="panel panel--navy">
    <h2 class="impact-title">THE IMPACT OF <span>YOUR GIFT</span></h2>
    <p class="impact-copy">Your generosity drives our mission. With every Smart gift you're supporting Meadowlark and Allied Services. Join our community of Smart Givers today and make an enduring impact. With Smart Giving your generosity reaches further. Begin your Smart Giving journey with us today.</p>
    <svg class="accent-triangle" width="70" height="181" viewBox="0 0 70 181" aria-hidden="true"><polygon points="35,0 70,181 0,181" fill="#fff"/></svg>
    <div class="photo photo--carers" role="img" aria-label="Photo of a smiling carer hugging an older woman seated in a wheelchair"></div>
    <ul class="options" style="list-style:none">
      <li class="option"><svg viewBox="0 0 16 16"><circle cx="8" cy="8" r="7.3" fill="#fff" stroke="#3cc13b" stroke-width="1"/><path d="M5 8.3l2 2 4-4.3" fill="none" stroke="#2b2170" stroke-width="1.2"/></svg>Stocks and<br>Securities</li>
      <li class="option"><svg viewBox="0 0 16 16"><circle cx="8" cy="8" r="7.3" fill="#fff" stroke="#3cc13b"/><path d="M4 6.5L8 4l4 2.5zM5 7.3v4M7 7.3v4M9 7.3v4M11 7.3v4M4 11.7h8" fill="none" stroke="#2b2170" stroke-width=".9"/></svg>DAFs</li>
      <li class="option"><svg viewBox="0 0 16 16"><circle cx="8" cy="8" r="7.3" fill="#fff" stroke="#3cc13b"/><rect x="5" y="7" width="6" height="5" fill="none" stroke="#2b2170" stroke-width=".9"/><path d="M4.5 7h7M8 7v5" stroke="#2b2170" stroke-width=".9"/></svg>QCDs</li>
      <li class="option"><svg viewBox="0 0 16 16"><circle cx="8" cy="8" r="7.3" fill="#fff" stroke="#3cc13b"/><circle cx="8" cy="8" r="4" fill="none" stroke="#2b2170" stroke-width=".9"/></svg>Crypto</li>
      <li class="option"><svg viewBox="0 0 16 16"><circle cx="8" cy="8" r="7.3" fill="#fff" stroke="#3cc13b"/><rect x="5" y="6" width="6" height="6" rx="1" fill="none" stroke="#2b2170" stroke-width=".9"/><path d="M8 10.5l-1.3-1.3a.8.8 0 0 1 1.3-1 .8.8 0 0 1 1.3 1z" fill="#2b2170"/></svg>Charitable<br>Annuity</li>
    </ul>
  </article>

  <article class="panel panel--navy">
    <p class="invite"><span class="hl">To learn more about Smart Giving Options and how they can benefit you and Meadowlark and</span> Allied Services, please reach out to our team. We're here to help you navigate these giving methods and answer any question you may have.</p>
    <blockquote class="quote"><span class="quote-mark quote-mark--open">&ldquo;</span>Being kind to others is a way of being good to yourself.<span class="quote-mark quote-mark--close">&rdquo;</span></blockquote>
    <p class="quote-author">-Miriam Holloway</p>
    <p class="will">If you do not have a will, go to<span class="will-url">www.EasyLegacyWill.com</span>In 20 minutes you can have a legal will – for free.</p>
    <div class="contact-box">
      <div class="contact-tab">CONTACT US</div>
      <p class="contact-head">Have more question?<small>Please contact us at Meadowlark and Allied Services</small></p>
      <ul class="contact-list">
        <li><svg viewBox="0 0 6 6"><path d="M3 .3a2 2 0 0 1 2 2C5 3.8 3 5.7 3 5.7S1 3.8 1 2.3a2 2 0 0 1 2-2z" fill="#3cc13b"/></svg>2150 Prairie View Rd., Suite 4, Fargo,<br>ND 58102</li>
        <li><svg viewBox="0 0 6 6"><path d="M1 .5l1.2 1.3-.6.8a4 4 0 0 0 1.8 1.8l.8-.6L5.5 5 4.7 5.6C2.5 5.3.7 3.5.4 1.3z" fill="#3cc13b"/></svg>701-555-0148 (ext. 100)</li>
        <li><svg viewBox="0 0 6 6"><rect x=".3" y="1" width="5.4" height="4" fill="#3cc13b"/><path d="M.3 1l2.7 2 2.7-2" fill="none" stroke="#2b2170" stroke-width=".5"/></svg>dmoreau@meadowlarkallied.org</li>
        <li><svg viewBox="0 0 6 6"><circle cx="3" cy="3" r="2.6" fill="none" stroke="#3cc13b" stroke-width=".6"/><path d="M.4 3h5.2M3 .4c-1.5 1.5-1.5 3.7 0 5.2M3 .4c1.5 1.5 1.5 3.7 0 5.2" fill="none" stroke="#3cc13b" stroke-width=".5"/></svg>www.meadowlarkallied.org</li>
      </ul>
      <div class="follow">Follow us<div class="social"><span></span><span></span></div></div>
      <p class="disclaimer">This material is for general information only and is not tax, legal or accounting advice. Please speak with your own tax adviser or financial professional before making any decision about Smart Giving.</p>
    </div>
  </article>

  <article class="panel panel--light">
    <p class="org-name"><span class="dot"></span>Meadowlark and<br>Allied Services</p>
    <h1 class="cover-title"><span class="l1">TRANSFORM</span><span class="l2">YOUR GIVING</span></h1>
    <p class="tagline">BE STRATEGIC<i>|</i>BE SMART</p>
    <p class="discover">Discover the impact of Smart Giving with Meadowlark and Allied Services</p>
    <div class="photo photo--couple" role="img" aria-label="Photo of a smiling older couple resting heads together at home"></div>
    <span class="float-icon" style="left:28px;top:150px"><svg viewBox="0 0 12 12"><circle cx="6" cy="6" r="4.5" fill="none" stroke="#3cc13b"/></svg></span>
    <span class="float-icon" style="left:163px;top:155px"><svg viewBox="0 0 12 12"><path d="M2 10V7M5 10V5M8 10V3M1 10.5h10" stroke="#3cc13b" stroke-width="1.2"/></svg></span>
    <span class="float-icon" style="left:22px;top:196px"><svg viewBox="0 0 12 12"><path d="M1.5 4.5L6 2l4.5 2.5zM3 5v4.5M5 5v4.5M7 5v4.5M9 5v4.5M1.5 10h9" fill="none" stroke="#2b2170" stroke-width=".8"/></svg></span>
    <span class="float-icon" style="left:181px;top:218px"><svg viewBox="0 0 12 12"><rect x="2.5" y="4" width="7" height="6" rx="1" fill="none" stroke="#2b2170" stroke-width=".8"/><circle cx="6" cy="2.5" r="1.3" fill="none" stroke="#2b2170" stroke-width=".7"/></svg></span>
    <p class="url-pill">www.meadowlarkallied.org</p>
  </article>
</section>

<!-- Inside spread -->
<section class="spread spread--inside">
  <article class="panel panel--white">
    <p class="intro">We would like to introduce you to five Strategic and Smart ways to give that could potentially be more beneficial to you compared to traditional cash donations. We encourage you to keep this information as a guide for your future contributions.</p>
    <header class="stocks-head">
      <p class="feature-kicker">Gifts of Stocks<br>or Appreciated</p>
      <p class="feature-main">Assets<br>Strategic &amp;<br>Smart</p>
    </header>
    <svg class="chart" viewBox="0 0 95 75" role="img" aria-label="Rising bar chart">
      <rect x="15" y="50" width="9" height="20" fill="#2ea82e"/>
      <rect x="28" y="42" width="9" height="28" fill="#2ea82e"/>
      <rect x="41" y="34" width="9" height="36" fill="#2ea82e"/>
      <rect x="54" y="25" width="9" height="45" fill="#2ea82e"/>
      <path d="M12 40L32 28L45 33L68 10" fill="none" stroke="#2ea82e" stroke-width="4"/>
      <polygon points="72,4 60,8 70,17" fill="#2ea82e"/>
    </svg>
    <div class="stocks-copy body-copy">
      <p><strong>Consider your long-term publicly traded stock as a way to give to your favorite charity.</strong></p>
      <p>You can make a significantly bigger impact when you donate long-term appreciated securities, including stock, mutual funds, and bonds, directly to your favorite charity.</p>
      <h4>How Does It Work?</h4>
      <p>When you donate stock to a charity, you will generally take a tax deduction for the full market value. Because you are donating stock, your contribution and tax deduction may be significantly higher than contributing the after-tax proceeds. The same benefits apply when you donate mutual funds or bonds.</p>
    </div>
  </article>

  <article class="panel panel--white">
    <header class="daf-head">
      <p class="feature-kicker">Donor-Advised<br>Fund (DAF)</p>
      <p class="feature-main">Strategic &amp;<br>Smart</p>
    </header>
    <div class="bank-art" role="img" aria-label="Illustration of a classical bank building"></div>
    <div class="daf-copy">
      <p><strong>Consider a DAF – a simple, flexible, and tax-advantageous way to give to your favorite charities.</strong></p>
      <p style="margin-top:3px">A Donor-Advised Fund (DAF), is like a charitable investment account for the sole purpose of supporting your favorite charities.</p>
      <h4>How Does It Work?</h4>
      <p>You establish a DAF and contribute cash, stocks, or non-publicly traded assets, cryptocurrency, and private company stock to be eligible for an immediate tax deduction. Those funds are contributed for tax-free growth. You can recommend grants be made from your DAF to any IRS qualified public charity.</p>
    </div>
    <div class="qcd-art" role="img" aria-label="Illustration of a hand holding a money bag"></div>
    <header class="qcd-head">
      <p class="feature-kicker">Qualified Charitable<br>Distributions (QCDs)</p>
      <p class="feature-main">Strategic &amp; Smart</p>
      <p>Consider a QCD – when planning your IRA withdrawal strategy...and donate to your favorite charity.</p>
    </header>
    <div class="qcd-copy">
      <p>IRA owners at age 70½ or over can transfer dollars from their IRA to charity tax-free each year. These transfers known as Qualified Charitable Distributions (QCDs) offer eligible older Americans a great way to easily give to charity.</p>
      <h4>How Does It Work?</h4>
      <p>Are you 72 and required to take a minimum distribution (RMD) from your IRA but do not need the funds? Consider a Qualified Charitable Distribution. Normally, distributions from a traditional IRA are taxable when received. With a QCD, these distributions become tax-free when paid directly from the IRA to your favorite eligible charity. An IRA owner wishing to make a QCD should contact their IRA trustee, allowing time to complete the transaction before the end of the year to receive the tax benefit.</p>
    </div>
  </article>

  <article class="panel panel--navy">
    <div class="gift-block gift-block--crypto">
      <div class="gift-head">
        <div class="gift-art gift-art--coin" role="img" aria-label="Illustration of a gold cryptocurrency coin"></div>
        <div>
          <p class="feature-kicker">Cryptocurrency</p>
          <p class="feature-main">Strategic &amp; Smart</p>
          <p>Consider donating Bitcoin and other cryptocurrencies to your favorite charity.</p>
        </div>
      </div>
      <div class="gift-copy">
        <p>Bitcoin and other cryptocurrencies can be donated to charity just like other appreciated assets such as stocks and other business interests. Before you sell bitcoin and donate the after-tax proceeds, consider donating your bitcoin directly to a favorite charity.</p>
        <h4>How Does It Work?</h4>
        <p>Many donors find it useful to open a Donor-Advised Fund (DAF). This strategy includes two significant benefits, both for you and your favorite charity.</p>
        <p>Your tax deduction will be equal to the fair market value of the donated bitcoin (as determined by a qualified appraisal).</p>
        <p>Your cryptocurrency donation is tax-smart because it may eliminate capital gains taxes on the value / appreciation AND your favorite charity will receive 100% of the value of the contribution.</p>
        <p>Often charities are not able to accept direct donations of bitcoin/crypto so using a DAF is a great way to donate these assets.</p>
      </div>
    </div>
    <div class="gift-block gift-block--annuity">
      <div class="gift-head">
        <div class="gift-art gift-art--box" role="img" aria-label="Illustration of a wrapped gift box"></div>
        <div>
          <p class="feature-kicker">Charitable Gift Annuity</p>
          <p class="feature-main">Strategic &amp; Smart</p>
          <p>Consider establishing a Charitable Gift Annuity</p>
        </div>
      </div>
      <div class="gift-copy">
        <p>You make a donation to a single charity. The gift is set aside in a reserve account and invested.</p>
        <h4>How Does It Work?</h4>
        <p>A charitable gift annuity is a contract between a donor and a charity. As a donor, you make a sizable gift to charity using cash, securities, or possibly other assets. This money is then invested. In return, you become eligible to take a partial tax deduction for your donation, plus you receive a fixed stream of income from the charity for the rest of your life (as well as your spouse's, if you're giving as a couple), the charity receives the remainder of the gift.</p>
      </div>
    </div>
  </article>
</section>

</body>
</html>
```